Vellisant - Quality health delivered at your door

Vellisant offers home and Community Based Services for adults who wish to continue live independently in their communities. We increase accessibility to health care, reduce health care delivery gap, reduce mortality and morbidity, reduce health while promoting healthy living in the comfort of our patients communities or homes.

We provide on site services and deliver high quality healthcare at your door. Our experienced physicians coordinate care with our certified nurse practitioners and provide chronic care management, physical therapy, rehabilitation and medications management.

Target Market(s)

Older population living in independent living facilities

Industry/Entity Type

Health Care

Contact Information for Business Card

Vellisant

Number of Pages Required

4 page

Font styles to use
Sans Serif

Colors

Designer to choose colors to be used in the design.

```html
<!DOCTYPE html>
<html lang="en">
<head>
<meta charset="utf-8">
<title>Vellisant – Quality health delivered at your door</title>
<link rel="stylesheet" href="https://fonts.googleapis.com/css2?family=Mulish:wght@400;600;700&display=swap">
<style>
:root{
  --green:#4a7a10;
  --green-light:#6f9e1c;
  --green-dark:#2f4f0c;
  --green-deep:#2d4a12;
  --orange:#f7941d;
  --orange-light:#fbb03b;
  --text:#333;
  --muted:#777;
  --grey-bg:#eeeeee;
  --white:#fff;
}
*{margin:0;padding:0;box-sizing:border-box}
html,body{width:1200px;height:2568px;overflow:hidden}
body{font-family:"Mulish",sans-serif;color:var(--text);background:var(--white);position:relative}
.abs{position:absolute}

/* header */
.brand{left:118px;top:14px;display:flex;align-items:center;gap:14px}
.brand-dot{width:84px;height:84px;border-radius:50%;background:var(--green)}
.brand-name{font-size:36px;font-weight:600;color:var(--green-deep);letter-spacing:.5px}
.top-links{left:664px;top:0;width:426px;height:36px;background:#ececec;clip-path:polygon(0 0,100% 0,96% 100%,4% 100%);font-size:12.5px;display:flex;align-items:center;justify-content:center;color:#444}
.top-links span{margin:0 6px}
.phone{left:886px;top:62px;font-size:23px;color:#444;display:flex;align-items:center;gap:8px}

/* nav */
.nav{left:0;top:118px;width:1200px;height:57px;background:linear-gradient(#79a82a,#4a7a10)}
.nav ul{list-style:none;display:flex;margin-left:118px;height:100%}
.nav li{color:var(--white);font-size:16px;font-weight:600;padding:0 16px;display:flex;align-items:center;border-right:1px solid rgba(255,255,255,.25)}
.nav li.active{background:var(--green-dark)}

/* hero */
.hero{left:0;top:175px;width:1200px;height:545px;background:linear-gradient(100deg,#e9eef1 0%,#dfe6ea 40%,#c9a98a 70%,#e8ddd2 100%)}
.hero-curve{left:0;top:660px;width:1200px}
.hero-title{left:120px;top:345px;font-size:37px;font-weight:700;line-height:43px}
.hero-title .o{color:var(--orange)}
.hero-title .g{color:var(--green)}
.btn-orange{left:121px;top:450px;width:154px;height:42px;background:var(--orange);color:var(--white);font-size:15px;display:flex;align-items:center;justify-content:center}
.dots{left:136px;top:521px;display:flex;gap:9px}
.dots i{width:17px;height:17px;border-radius:50%;border:2px solid #bbb;background:var(--white)}

/* welcome */
.welcome-title{left:0;top:742px;width:1200px;text-align:center;font-size:31px;letter-spacing:1px;color:#222}
.welcome-text{left:220px;top:803px;width:760px;text-align:center;font-size:16px;line-height:29px;color:#555}
.btn-green{left:513px;top:983px;width:155px;height:42px;background:linear-gradient(#5f8f1c,#3e6a0c);color:var(--white);font-size:15px;display:flex;align-items:center;justify-content:center}

/* services */
.services{left:0;top:1118px;width:1200px;height:688px;background:linear-gradient(90deg,#e6e6e6,#f1f1f1 50%,#e4e4e4);border-top:1px solid #ccc}
.services-photo{left:0;top:1118px;width:1200px;height:688px;background:radial-gradient(ellipse at 40% 40%,rgba(220,200,190,.45),rgba(240,240,240,0) 60%)}
.badge{left:570px;top:1088px;width:60px;height:60px;border-radius:50%;background:var(--white);box-shadow:0 2px 6px rgba(0,0,0,.2);display:flex;align-items:center;justify-content:center}
.badge i{width:46px;height:46px;border-radius:50%;background:var(--green)}
.services-title{left:0;top:1166px;width:1200px;text-align:center;font-size:28px;color:var(--green)}
.service{width:310px;display:flex;gap:12px}
.s-icon{flex:none;width:82px;height:82px;border-radius:50%;background:var(--orange);border:3px solid var(--green);display:flex;align-items:center;justify-content:center}
.s-icon svg{width:46px;height:46px;fill:none;stroke:var(--white);stroke-width:2.5;stroke-linecap:round;stroke-linejoin:round}
.s-name{font-size:19px;line-height:25px;color:#222;margin-top:-2px}
.s-text{font-size:12.5px;line-height:19px;color:#888;margin-top:4px}
.s-more{font-size:13.5px;font-weight:700;color:var(--green);margin-top:6px}
.btn-outline{left:488px;top:1602px;width:226px;height:44px;border:2px solid var(--green-dark);color:var(--green-dark);font-size:15px;font-weight:600;display:flex;align-items:center;justify-content:center}

/* cards */
.card{top:1710px;width:300px;height:360px;background:var(--white);border:1px solid #ccc}
.card-img{height:190px}
.card-label{height:47px;padding-left:20px;font-size:22px;color:var(--white);display:flex;align-items:center}
.card-text{padding:14px 20px 0;font-size:12.5px;line-height:19px;color:#777}
.card-more{padding:6px 20px;font-size:14px;font-weight:600;color:var(--green-dark)}

/* footer */
.footer{left:0;top:2148px;width:1200px;height:352px;background:linear-gradient(var(--orange-light),var(--orange))}
.f-logo{left:134px;top:2194px;width:200px;text-align:center}
.f-logo i{display:block;width:140px;height:140px;margin:0 auto 14px;border-radius:50%;background:var(--green);border:5px solid var(--white)}
.f-logo span{font-size:35px;font-weight:600;color:var(--green-deep)}
.f-col{top:2212px;color:var(--white)}
.f-col h3{font-size:20px;font-weight:400;margin-bottom:14px}
.f-col p{font-size:14.5px;line-height:30px}
.contact-row{display:flex;gap:12px;align-items:flex-start}
.contact-row svg{flex:none;width:18px;height:18px;margin-top:6px;fill:none;stroke:var(--white);stroke-width:2}
.socials{display:flex;gap:8px;margin-top:12px}
.socials i{width:32px;height:32px;border-radius:50%;border:2px solid var(--white)}
.bottom{left:0;top:2500px;width:1200px;height:68px;background:var(--green-deep);color:var(--white);font-size:12.5px;display:flex;align-items:center;justify-content:center}
</style>
</head>
<body>

<header>
  <div class="abs brand"><i class="brand-dot"></i><span class="brand-name">VELLISANT</span></div>
  <div class="abs top-links"><span>Rehabilitation</span>|<span>Memora Learning</span>|<span>Center</span>|<span>Memora Learning</span></div>
  <div class="abs phone">
    <svg width="22" height="22" viewBox="0 0 24 24"><path fill="#f7941d" d="M6.6 10.8a15 15 0 0 0 6.6 6.6l2.2-2.2c.3-.3.7-.4 1-.2 1.1.4 2.3.6 3.6.6.6 0 1 .4 1 1V20c0 .6-.4 1-1 1A17 17 0 0 1 3 4c0-.6.4-1 1-1h3.5c.6 0 1 .4 1 1 0 1.3.2 2.5.6 3.6.1.3 0 .7-.2 1z"/></svg>
    (685) 555 0172
  </div>
  <nav class="abs nav"><ul>
    <li class="active">Home</li><li>Assisted Living</li><li>Skilled Nursing</li><li>Independent Living</li><li>Community Based Services</li><li>Respite Care</li>
  </ul></nav>
</header>

<section>
  <div class="abs hero" role="img" aria-label="Photo of a smiling nurse caring for an elderly woman resting in bed"></div>
  <svg class="abs hero-curve" width="1200" height="62" viewBox="0 0 1200 62"><path d="M0 62 L0 40 Q600 -30 1200 42 L1200 62 Z" fill="#fff"/><path d="M0 40 Q600 -30 1200 42" fill="none" stroke="#cfcfcf" stroke-width="2"/></svg>
  <h1 class="abs hero-title"><span class="o">SKILLED NURSING &amp;</span><br><span class="g">HOME CARE SERVICES</span></h1>
  <div class="abs btn-orange">READ MORE</div>
  <div class="abs dots"><i></i><i></i><i></i><i></i></div>
</section>

<section>
  <h2 class="abs welcome-title">WELCOME TO OUR WEBSITE</h2>
  <p class="abs welcome-text">Vellisant offers home and Community Based Services for adults who wish to continue to live independently in the comfort of their communities.<br>We provide on site services and deliver high quality healthcare at your door. Our experienced physicians coordinate care with our certified nurse practitioners and provide chronic care management, physical therapy, rehabilitation and medications management.</p>
  <div class="abs btn-green">READ MORE</div>
</section>

<section>
  <div class="abs services"></div>
  <div class="abs services-photo" role="img" aria-label="Faint background photo of a caregiver assisting an elderly patient"></div>
  <div class="abs badge"><i></i></div>
  <h2 class="abs services-title">OUR SERVICES</h2>

  <div class="abs service" style="left:113px;top:1248px">
    <div class="s-icon"><svg viewBox="0 0 48 48"><path d="M6 20c4 10 10 16 18 18 8-2 14-8 18-18"/><path d="M12 24c3 5 7 8 12 9 5-1 9-4 12-9"/></svg></div>
    <div><div class="s-name">Comprehensive primary Care Services</div><div class="s-text">Morbi diam mauris viverra in gravida eu mattis in ante Morbi eget arcu</div><div class="s-more">Read More</div></div>
  </div>
  <div class="abs service" style="left:446px;top:1248px">
    <div class="s-icon"><svg viewBox="0 0 48 48"><path d="M24 40 8 24a9 9 0 0 1 16-11 9 9 0 0 1 16 11z"/><path d="M6 24h10l3-6 5 12 3-6h15"/></svg></div>
    <div><div class="s-name">Coordination of Speciality Care</div><div class="s-text">Morbi diam mauris viverra in gravida eu mattis in ante Morbi eget arcu</div><div class="s-more">Read More</div></div>
  </div>
  <div class="abs service" style="left:762px;top:1248px">
    <div class="s-icon"><svg viewBox="0 0 48 48"><circle cx="24" cy="24" r="9"/><path d="M24 6v6M24 36v6M6 24h6M36 24h6M11 11l4 4M33 33l4 4M37 11l-4 4M15 33l-4 4"/></svg></div>
    <div><div class="s-name">Chronic Disease Management</div><div class="s-text">Morbi diam mauris viverra in gravida eu mattis in ante Morbi eget arcu</div><div class="s-more">Read More</div></div>
  </div>

  <div class="abs service" style="left:113px;top:1425px">
    <div class="s-icon"><svg viewBox="0 0 48 48"><path d="M32 8l8 8M36 12 16 32l-6-6 20-20M10 38l6-6M22 18l4 4M18 22l4 4"/></svg></div>
    <div><div class="s-name">Transitional Care</div><div class="s-text">Morbi diam mauris viverra in gravida eu mattis in ante Morbi eget arcu Class aptent taciti sociosqu ad litora torquent</div><div class="s-more">Read More</div></div>
  </div>
  <div class="abs service" style="left:446px;top:1425px">
    <div class="s-icon"><svg viewBox="0 0 48 48"><rect x="8" y="14" width="32" height="24" rx="4"/><path d="M18 14v-4h12v4M24 20v12M18 26h12"/></svg></div>
    <div><div class="s-name">Skilled nursing visits for Wound Care</div><div class="s-text">Morbi diam mauris viverra in gravida eu mattis in ante Morbi eget arcu</div><div class="s-more">Read More</div></div>
  </div>
  <div class="abs service" style="left:762px;top:1425px">
    <div class="s-icon"><svg viewBox="0 0 48 48"><path d="M6 24 24 8l18 16M12 20v20h24V20M24 24v10M19 29h10"/></svg></div>
    <div><div class="s-name">Home Health Assistance</div><div class="s-text">Morbi diam mauris viverra in gravida eu mattis in ante Morbi eget arcu</div><div class="s-more">Read More</div></div>
  </div>

  <div class="abs btn-outline">VIEW MORE SERVICES</div>
</section>

<section>
  <article class="abs card" style="left:116px">
    <div class="card-img" role="img" aria-label="Photo of a caregiver with an elderly man in a wheelchair" style="background:linear-gradient(135deg,#9cc3b0,#d9c3a8)"></div>
    <div class="card-label" style="background:var(--orange)">Assisted Living</div>
    <p class="card-text">Class aptent taciti sociosqu ad litora torquent per conubia nostra per inceptos hymenaeos Proin nulla arcu nonummy luctus</p>
    <div class="card-more">READ MORE</div>
  </article>
  <article class="abs card" style="left:443px">
    <div class="card-img" role="img" aria-label="Photo of a therapist helping an elderly man with rehabilitation" style="background:linear-gradient(135deg,#e3ddd4,#b7aa9a)"></div>
    <div class="card-label" style="background:var(--green-light)">Rehabilitation</div>
    <p class="card-text">Class aptent taciti sociosqu ad litora torquent per conubia nostra per inceptos hymenaeos Proin nulla arcu nonummy luctus</p>
    <div class="card-more">READ MORE</div>
  </article>
  <article class="abs card" style="left:771px">
    <div class="card-img" role="img" aria-label="Photo of a young carer with a smiling elderly woman" style="background:linear-gradient(135deg,#d5dde2,#e6b9a6)"></div>
    <div class="card-label" style="background:var(--green-deep)">Respite Care</div>
    <p class="card-text">Class aptent taciti sociosqu ad litora torquent per conubia nostra per inceptos hymenaeos Proin nulla arcu nonummy luctus</p>
    <div class="card-more">READ MORE</div>
  </article>
</section>

<footer>
  <div class="abs footer"></div>
  <div class="abs f-logo"><i></i><span>VELLISANT</span></div>
  <div class="abs f-col" style="left:431px">
    <h3>QUICK LINKS</h3>
    <p>Home<br>Assisted Living<br>Skilled Nursing<br>Independent Living<br>Home and Community<br>Based Services</p>
  </div>
  <div class="abs f-col" style="left:646px">
    <h3>SERVICES</h3>
    <p>Respite Care<br>Rehabilitation<br>Memora Learning Center<br>Memora Learning®</p>
  </div>
  <div class="abs f-col" style="left:855px">
    <h3>CONTACT US</h3>
    <div class="contact-row"><svg viewBox="0 0 24 24"><path d="M12 22s7-7 7-12a7 7 0 0 0-14 0c0 5 7 12 7 12z"/><circle cx="12" cy="10" r="2.5"/></svg><p>48 Linden Avenue #4B<br>Texas 75201 TX</p></div>
    <div class="contact-row"><svg viewBox="0 0 24 24"><path d="M6.6 10.8a15 15 0 0 0 6.6 6.6l2.2-2.2 4.6 1V20A17 17 0 0 1 4 4h4l1 4.6z"/></svg><p>586.555.0143</p></div>
    <div class="contact-row"><svg viewBox="0 0 24 24"><rect x="3" y="5" width="18" height="14" rx="1"/><path d="m3 6 9 7 9-7"/></svg><p>info@vellisant-care.com</p></div>
    <div class="socials"><i></i><i></i><i></i><i></i></div>
  </div>
  <div class="abs bottom">© 2017 Vellisant &nbsp;All right reserved &nbsp;Term of Use</div>
</footer>

</body>
</html>
```